Accountant website

Please design a accountant website for www.fenwaybridgeadvisory.com.au. This site is majorly out of date, and is not supported by modern browsers.

The style should use the reds from the design at dev.fenwaybridgeadvisory.com.au, and should be modern and make use of Slides (large content slides that the user scrolls through on the front page).

The content is largely already on the site, however happy to move some around to suit the modern design as required.

The dev.fenwaybridgeadvisory.com.au was a rough mock up that I have completed that the client is "happy" with the direction, however this needs a lot of polish and finishing touches, and I will accept designs that differ from this, but highly recommend that this is used as a guide.

Ready to be sliced PSD Only - HTML no required.

In all honesty, although I can technically do a lot of this, the polished finished I want for this site has eluded me in a few attempts, and therefore I am looking out there at you much more artistic people to finish (or redesign if required) this site.

Target Market(s)

Higher end Small - Medium Business

Industry/Entity Type

Accountant

Requirements
Must have
• Must use the logo from dev.fenwaybridgeadvisory.com.au use exactly the red colours as defined in this layout. A basic layout PSD (to get the colour etc) and the logo in ai format is attached to this project. Please ignore the SSL warning on the development site.

The final product does NOT have to be the same as shown on dev.fenwaybridgeadvisory.com.au however the red colour scheme must be used. The client DOES want the logo on the RIGHT.

Must have a front landing page design, and a page layout that considers the other page content (at least one separate PSD)
Nice to have
• I really am looking at a slide format for the front page simular to:

http://www.quillo.com/au/
http://www.vaultmoor.com/

The attached photos should be used on the site. Was considering a rotating banner with these images are a watermark background on a solid Red header bar, but happy to be shown other options.
Should not have
• Please no "Layout Goblin" submissions.

```html
<!DOCTYPE html>
<html lang="en">
<head>
<meta charset="utf-8">
<title>Fenway Bridge Advisory</title>
<link rel="stylesheet" href="https://fonts.googleapis.com/css2?family=Bitter:wght@400;700&family=Open+Sans:wght@400;600;700&family=Oswald:wght@400;500&display=swap">
<style>
:root{
  --red:#c1272d;
  --red-dark:#9e1e23;
  --ink:#2b2b2b;
  --text:#555;
  --grey-nav:#4d4f52;
  --grey-nav-dark:#3a3c3f;
  --panel:#f3f3f3;
  --line:#d4d4d4;
  --footer:#26272a;
  --footer-text:#e5e5e5;
  --white:#fff;
}
*{box-sizing:border-box;margin:0;padding:0}
html,body{width:1200px;height:2219px;overflow:hidden;background:var(--white)}
body{position:relative;font-family:"Open Sans",Arial,sans-serif;color:var(--text)}
.abs{position:absolute}

/* header */
.brand{left:790px;top:22px;width:310px;text-align:right;font-family:"Bitter",Georgia,serif;font-weight:700;color:var(--ink);font-size:38px;line-height:40px;letter-spacing:1px}
.brand small{display:block;font-size:18px;line-height:24px;letter-spacing:2px}
.hero{left:0;top:166px;width:1200px;height:492px;background:linear-gradient(180deg,#b9c7d3 0%,#8a98a6 35%,#6c6e72 65%,#9b9a95 100%)}
.nav{left:100px;top:138px;width:998px;height:48px;display:flex;z-index:2;box-shadow:0 2px 4px rgba(0,0,0,.35)}
.nav a{display:flex;align-items:center;justify-content:center;font-family:"Bitter",Georgia,serif;font-size:17px;color:var(--white);text-decoration:none;background:linear-gradient(var(--grey-nav),var(--grey-nav-dark));border-right:1px solid #2c2d2f}
.nav a.active{background:linear-gradient(#d13238,var(--red-dark))}
.caption{left:100px;top:506px;width:730px;height:152px;background:rgba(255,255,255,.78)}
.caption svg{position:absolute;left:728px;top:0}
.caption h1{position:absolute;left:18px;top:14px;font-family:"Oswald",Arial,sans-serif;font-weight:500;font-size:50px;color:#333;letter-spacing:-.5px}
.caption p{position:absolute;left:18px;top:82px;font-family:"Oswald",Arial,sans-serif;font-size:35px;color:var(--red);white-space:nowrap}
.dots{left:756px;top:548px;display:flex;gap:10px}
.dots span{width:15px;height:15px;border-radius:50%;background:#555}
.dots span.on{background:var(--red)}

/* intro */
.intro{left:100px;top:718px;width:600px}
.intro h2{font-family:"Bitter",Georgia,serif;font-weight:400;font-size:26px;color:var(--ink);margin-bottom:14px}
.intro p{font-size:14.5px;line-height:22px;padding-left:4px}

/* features */
.feature{left:100px;width:600px;height:210px}
.feature .photo{position:absolute;left:0;top:0;width:202px;height:202px;border-radius:50%;border:6px solid #cfcfcf}
.feature .num{position:absolute;left:166px;top:20px;width:52px;height:52px;border-radius:50%;background:var(--red);border:4px solid var(--white);color:var(--white);font-family:"Bitter",Georgia,serif;font-size:22px;display:flex;align-items:center;justify-content:center}
.feature h3{position:absolute;left:224px;top:28px;font-family:"Bitter",Georgia,serif;font-weight:400;font-size:26px;color:var(--ink);white-space:nowrap}
.feature p{position:absolute;left:226px;top:72px;width:365px;font-size:13.5px;line-height:21px}

/* sidebar */
.team{left:759px;top:676px;width:338px;height:224px;border:2px solid var(--red);padding:5px;background:var(--white)}
.team div{width:100%;height:100%;background:linear-gradient(180deg,#b12a2e 0%,#c9484b 45%,#e7e3df 70%,#f4f4f4 100%)}
.quote-form{left:759px;top:919px;width:338px;height:310px;border:10px solid var(--red);background:var(--white);padding:14px 14px 0}
.quote-form .q{font-size:12px;color:#444}
.slider{position:relative;height:52px}
.slider .track{position:absolute;left:0;right:0;top:18px;height:8px;border-radius:4px;background:#e3e3e3;border:1px solid #ccc}
.slider .thumb{position:absolute;left:62px;top:13px;width:18px;height:18px;border-radius:50%;background:var(--red)}
.slider .l{position:absolute;top:34px;font-size:12px;color:#999;font-weight:600}
.slider .val{left:50px;color:#222;font-weight:700;font-size:13px}
.field{display:flex;align-items:center;height:42px}
.field label{width:72px;font-size:12.5px;color:#222}
.field span{width:210px;height:32px;background:#ececec;border:1px solid #c9c9c9}
.field span.short{width:158px}
.apply{left:848px;top:1213px;width:160px;height:34px;background:linear-gradient(#cf3035,var(--red-dark));color:var(--white);font-size:13px;font-weight:600;display:flex;align-items:center;justify-content:center;letter-spacing:.5px;box-shadow:0 2px 3px rgba(0,0,0,.3)}
.promo{left:759px;width:338px;height:185px;background:#eef0f1;border-bottom:3px solid #c7c7c7}
.promo .pic{position:absolute;top:0;height:100%}
.promo h4{position:absolute;font-family:"Open Sans",Arial,sans-serif;font-weight:400;font-size:30px;color:#555}
.promo p{position:absolute;font-size:13px;line-height:18px;color:#555}
.btn{position:absolute;height:30px;padding:0 14px;background:linear-gradient(#cf3035,var(--red-dark));color:var(--white);font-size:16px;display:flex;align-items:center;box-shadow:0 1px 3px rgba(0,0,0,.35)}
.clients{left:759px;top:1730px;width:338px}
.clients h4{font-family:"Bitter",Georgia,serif;font-weight:400;font-size:25px;color:var(--ink);padding-left:15px;margin-bottom:12px}
.clients blockquote{position:relative;background:var(--panel);padding:16px 16px;font-size:13px;line-height:22px;color:#555}
.clients blockquote svg{position:absolute;left:24px;bottom:-22px}
.clients cite{display:block;margin:14px 0 0 65px;font-family:"Bitter",Georgia,serif;font-style:normal;font-size:16px;color:#555}

/* footer */
.footer{left:0;top:1980px;width:1200px;height:198px;background:var(--footer)}
.footer h5{font-family:"Bitter",Georgia,serif;font-size:17px;color:var(--white);font-weight:700}
.links{position:absolute;top:60px;list-style:none;font-size:15px;color:var(--footer-text);line-height:30px}
.links li::before{content:"";display:inline-block;width:5px;height:5px;background:#aaa;margin:0 8px 3px 0}
.news p{font-size:13.5px;line-height:20px;color:var(--footer-text);margin:6px 0 14px}
.news .email{width:275px;height:36px;background:var(--white);font-size:13px;color:#666;padding:9px 12px}
.news .sub{margin-top:12px;width:122px;height:34px;background:linear-gradient(#cf3035,var(--red-dark));color:var(--white);font-size:14px;font-weight:700;display:flex;align-items:center;justify-content:center;letter-spacing:1px}
.foot-brand{left:900px;top:26px;font-family:"Bitter",Georgia,serif;font-weight:700;font-size:31px;line-height:32px;color:#dcdcdc}
.foot-brand small{display:block;font-size:15px;letter-spacing:1.5px;line-height:20px}
.badge{left:895px;top:104px;width:200px;height:62px;border:2px solid #9a9a9a;border-radius:31px}
.bottom{left:100px;top:2186px;font-size:14px;color:#444}
.social{left:965px;top:2186px;display:flex;gap:12px}
.social span{width:24px;height:24px;border-radius:4px;background:var(--red)}
</style>
</head>
<body>

<div class="abs brand">FENWAY BRIDGE<small>ADVISORY</small></div>

<div class="abs hero" role="img" aria-label="Marina wharf with fishing boats, a consultant in a red dress walking along the pier"></div>

<nav class="abs nav">
  <a class="active" style="width:138px">About</a>
  <a style="width:129px">Services</a>
  <a style="width:191px">Working with Us</a>
  <a style="width:158px">Testimonials</a>
  <a style="width:235px">Article of the&nbsp; Moment</a>
  <a style="width:147px;border-right:0">Client Login</a>
</nav>

<div class="abs caption">
  <h1>BUSINESS CAN BE HARD</h1>
  <p>But we make detailed analysis of your finances easy</p>
  <svg width="80" height="152" viewBox="0 0 80 152" aria-hidden="true">
    <polygon points="0,0 24,0 72,76 24,152 0,152 0,150 46,76 0,2" fill="rgba(255,255,255,.78)"/>
    <polygon points="20,0 32,0 80,76 32,152 20,152 66,76" fill="#c1272d"/>
  </svg>
</div>
<div class="abs dots"><span></span><span class="on"></span><span></span></div>

<section class="abs intro">
  <h2>Getting to Know Fenway Bridge Advisory</h2>
  <p>Fenway Bridge Advisory aims to service the needs of its clients by focusing on the present rather than reporting on historical figures. We recognise that business owners benefit from regular contact with their accountant. One who undertakes a hands on approach in working with business owners to improve their business.</p>
</section>

<article class="abs feature" style="top:959px">
  <div class="photo" role="img" aria-label="Red target with arrows in the bullseye" style="background:radial-gradient(circle,#e9e9e9,#f7f7f7 60%,#d9d9d9)"></div>
  <div class="num">1</div>
  <h3>Believing in the here and now:</h3>
  <p>A proactive accountant that focuses on providing timely and relevant information.<br>This means... informed decisions can be made, accurate forecasts, industry comparisons, and other key diagnostic tools can be produced to ensure the performance of your business is always tracked and geared towards improvement.</p>
</article>

<article class="abs feature" style="top:1215px">
  <div class="photo" role="img" aria-label="Hand signing a document with a fountain pen" style="background:linear-gradient(135deg,#d9d4cc,#f2f0ec 55%,#c8c2b8)"></div>
  <div class="num">2</div>
  <h3>Monthly Billing to plan by:</h3>
  <p>Annual fees, agreed upon and broken down into 12 easy monthly instalments.<br><br>This means... no nasty surprises, your accounting budget is planned for the entire year. There are no unexpected bulk bills and it assists with cash flow management.</p>
</article>

<article class="abs feature" style="top:1469px">
  <div class="photo" role="img" aria-label="Silhouettes of business people in front of a blue globe" style="background:radial-gradient(circle at 45% 40%,#8fc7ef,#2c78c4 60%,#1b4f8f)"></div>
  <div class="num">3</div>
  <h3>Your&nbsp; Place in your time:</h3>
  <p>Monthly Billing: An accountant that delivers! Saving you travel time and stress.<br><br>This means... that your time can be better- spent on achieving your professional and personal goals. Furthermore, all of the required information is on hand, thus enabling efficiency in resolving business matters, and/or implementing business improvement measures.</p>
</article>

<article class="abs feature" style="top:1725px">
  <div class="photo" role="img" aria-label="Smiling support agent wearing a headset" style="background:linear-gradient(180deg,#d8d8d8,#b9b4b0 55%,#a8282d)"></div>
  <div class="num">4</div>
  <h3>We will actually call you back:</h3>
  <p>Responsiveness: Fenway Bridge Advisory offers a communication guarantee, all correspondence will be responded to within 24 hrs.<br><br>This means... less time is wasted waiting on a reply, opportunities can be seized faster and any issues can be resolved before they become a potential business threat.</p>
</article>

<aside>
  <div class="abs team"><div role="img" aria-label="The team seated at the reception desk beneath the firm's sign"></div></div>

  <form class="abs quote-form">
    <div class="q">How much cash do you need?</div>
    <div class="slider">
      <div class="track"></div><div class="thumb"></div>
      <span class="l" style="left:0">$0</span>
      <span class="l val">$80,000</span>
      <span class="l" style="right:0">$500,000</span>
    </div>
    <div class="field"><label>First name</label><span></span></div>
    <div class="field"><label>Last name</label><span></span></div>
    <div class="field"><label>Phone #</label><span></span></div>
    <div class="field"><label>Zip Code</label><span class="short"></span></div>
  </form>
  <div class="abs apply">APPLY NOW</div>

  <div class="abs promo" style="top:1292px">
    <div class="pic" role="img" aria-label="Smiling support agent wearing a headset" style="left:178px;width:160px;background:linear-gradient(90deg,#eef0f1,#d9dee2 40%,#c7b3a3)"></div>
    <h4 style="left:13px;top:36px">Need Help?</h4>
    <p style="left:13px;top:81px">Quisque ac ipsum lorem.<br>Vivamus hendreit nulla id</p>
    <div class="btn" style="left:30px;top:135px">CHAT NOW</div>
  </div>

  <div class="abs promo" style="top:1512px">
    <div class="pic" role="img" aria-label="Young professional in a dark suit and tie" style="left:0;width:170px;background:linear-gradient(180deg,#eef0f1 0%,#d2c6bd 35%,#2a2a2c 60%,#1e1e20)"></div>
    <h4 style="left:178px;top:28px;font-size:34px">Careers</h4>
    <p style="left:178px;top:80px">Quisque ac ipsum lorem.<br>Vivamus hendreit nulla id</p>
    <div class="btn" style="left:181px;top:128px;font-size:14px;font-weight:600">CLICK HERE</div>
  </div>

  <section class="abs clients">
    <h4>What Client's Say ?</h4>
    <blockquote>Lorem ipsum dolor sit amet, consectetuer adipiscing elit, sed diam nonummy nibh euismod tincidunt ut laoreet dolore magna aliquam erat volutpat.
      <svg width="30" height="22" viewBox="0 0 30 22" aria-hidden="true"><polygon points="0,0 30,0 22,22" fill="#f3f3f3"/></svg>
    </blockquote>
    <cite>Tom Hale</cite>
  </section>
</aside>

<footer class="abs footer">
  <h5 class="abs" style="left:100px;top:18px">Quick Links</h5>
  <ul class="links" style="left:100px">
    <li>About Us</li><li>Services</li><li>Working with us</li><li>Contact Us</li>
  </ul>
  <ul class="links" style="left:286px">
    <li>Testimonials</li><li>News</li><li>Articles Of the Moment</li><li>Client Login</li>
  </ul>
  <div class="abs news" style="left:530px;top:18px;width:320px">
    <h5>Subscribe for Newsletter</h5>
    <p>Lorem Ipsum dolor sit amet, consectetur<br>do elusmod tempor Incididunt ut labore et dolore</p>
    <div class="email">E-mail Address</div>
    <div class="sub">SUBSCRIBE</div>
  </div>
  <div class="abs foot-brand">FENWAY BRIDGE<small>ADVISORY</small></div>
  <div class="abs badge" aria-label="Professional accreditation badge"></div>
</footer>

<p class="abs bottom">© 2013 fenwaybridgeadvisory&nbsp; |&nbsp; All rights reserved.</p>
<div class="abs social" aria-label="Social links"><span></span><span></span><span></span></div>

</body>
</html>
```